Business Card Design for Vintage Jazz

I am a vintage jazz band leader in New York City. My groups play the music of the 1920s, 1930s and 1940s. My website is morvalquist.com for more info on what I do.

I am looking for a two sided business card design that has the look and feel of a really nice business card from the 1930s. I need to convey with the design that my work has that vintage kind of class and style, but also conveys that we are fun and entertaining.

Most importantly it should make a bold staement. If Hal Denbrook had a card, what would it have looked like? I want a card that I feel confident will make an impact and will let people know that my work is te the top that NYC has to offer in vintage jazz..

Note that I have only decided to avoid the "committed payment" option as I have not used this service before. Assuming that I get quality work I will select a design from those presented.

Target Market(s)

people who want to hire my band for events, media, and new fans of the band

Industry/Entity Type

Performing Art

Contact Information for Business Card

Definitely a matte finish, possibly a sort of old style of paper with that brown tint? definitely a thick card.

Requirements
Must have
• FRONT
• My name: Tobin Vashley
• What I do: Bandleader, Guitarist, Vocalist, Songwriter
• Contact Details: morvalquist.com tobin@morvalquist.com 646-555-0148
• BACK
• My Social Media Links:
• facebook.morvalquist.com
• twitter, instagram, linkedin: morvalquist
• I'm also including a photo image I would like to use. The photo's background is not needed, and to be honest isn't really desireable. Just looking to use the image of me.
Nice to have
• I'm attaching which could be used as is, omitted from the card, or altered maybe with text going around the outside of the circle or in some other way. It may need some clean up to the edges of the lettering as we only use it for the website thumbnail.
• If there's space I'd like to include the text "join our mailing list for a free song download: freesong.morvalquist.com" If not perhaps just "Download a Free Song at: freesong.morvalquist.com - something to this end.
Should not have
• anything cartoony. Don't think retro 90s's vision of the swing era, think actual swing era!
• anything modern. Got to look old school
• Try to avoid dark backgrounds. Since we often play in bars and clubs where it is dar, a d
• avoid script fonts.

```html
<!DOCTYPE html>
<html lang="en">
<head>
<meta charset="utf-8">
<title>Tobin Vashley – Business Card</title>
<link rel="stylesheet" href="https://fonts.googleapis.com/css2?family=Arimo:wght@400;700&display=swap">
<style>
  :root {
    --backdrop: #e9e4da;
    --cream: #fdf0cf;
    --teal: #4ecfb5;
    --ink: #111111;
    --night: #050505;
    --paper-white: #f4f4f4;
    --grey-light: #d9d9d9;
    --grey-dark: #2a2a2a;
  }
  * { box-sizing: border-box; margin: 0; padding: 0; }
  html, body {
    width: 1200px; height: 892px; overflow: hidden;
    background: var(--backdrop);
    font-family: "Arimo", Arial, sans-serif;
  }
  .canvas { position: relative; width: 1200px; height: 892px; }
  .card {
    position: absolute; width: 660px; height: 375px;
    box-shadow: 0 10px 24px rgba(0,0,0,.25);
    overflow: hidden;
  }
  .card-front { left: 50px; top: 60px; background: var(--cream); }
  .card-back { left: 490px; top: 457px; background: var(--night); }
  .card svg { position: absolute; inset: 0; }

  .name {
    position: absolute; right: 38px; top: 44px;
    font-size: 36px; font-weight: 700; color: var(--ink); letter-spacing: -0.5px;
  }
  .roles {
    position: absolute; right: 38px; top: 122px; text-align: right;
    font-size: 22px; font-weight: 700; line-height: 28px; color: var(--ink);
  }
  .contacts {
    position: absolute; right: 30px; top: 222px; list-style: none; text-align: right;
  }
  .contacts li {
    display: flex; justify-content: flex-end; align-items: center; gap: 10px;
    font-size: 18px; line-height: 27px; color: var(--ink);
  }
  .contacts .icon {
    width: 15px; height: 15px; background: var(--ink); border-radius: 2px;
    display: inline-block;
  }

  .brand-mark {
    position: absolute; left: 40px; top: 70px; width: 300px; height: 235px;
    display: flex; align-items: center; gap: 18px;
  }
  .brand-mark .ring {
    width: 90px; height: 90px; border: 6px solid var(--paper-white); border-radius: 50%;
    flex: none;
  }
  .brand-mark .brand-name {
    font-size: 34px; font-weight: 700; color: var(--paper-white); line-height: 38px;
  }
  .socials {
    position: absolute; right: 40px; top: 150px; color: var(--paper-white);
  }
  .socials .site { font-size: 30px; display: block; text-align: right; }
  .socials .handle { font-size: 30px; display: block; text-align: right; margin-top: 14px; }
  .social-icons { display: flex; justify-content: flex-end; gap: 16px; margin-top: 22px; }
  .social-icons span {
    width: 34px; height: 28px; background: var(--paper-white); display: block;
  }
</style>
</head>
<body>
<main class="canvas">
  <section class="card card-front" aria-label="Card front">
    <svg width="660" height="375" viewBox="0 0 660 375">
      <defs>
        <linearGradient id="portraitTone" x1="0" y1="0" x2="1" y2="1">
          <stop offset="0" stop-color="var(--grey-light)"/>
          <stop offset="0.5" stop-color="#6b6b6b"/>
          <stop offset="1" stop-color="var(--grey-dark)"/>
        </linearGradient>
      </defs>
      <polygon class="teal-frame" points="14,120 218,120 218,32 660,32 660,100 390,100 390,350 14,350"
               fill="var(--teal)" stroke="var(--ink)" stroke-width="3"/>
      <rect class="portrait" x="60" y="150" width="300" height="200" rx="40" fill="url(#portraitTone)"
            role="img" aria-label="Black and white portrait of the bandleader in a striped blazer tipping a straw boater hat"/>
    </svg>
    <h1 class="name">Tobin Vashley</h1>
    <p class="roles">Bandleader, Guitarist,<br>Vocalist, Songwriter</p>
    <ul class="contacts">
      <li>646-555-0148 <span class="icon"></span></li>
      <li>morvalquist.com <span class="icon"></span></li>
      <li>tobin@morvalquist.com <span class="icon"></span></li>
    </ul>
  </section>

  <section class="card card-back" aria-label="Card back">
    <div class="brand-mark">
      <span class="ring"></span>
      <span class="brand-name">Tobin<br>Vashley</span>
    </div>
    <div class="socials">
      <span class="site">morvalquist.com</span>
      <span class="handle">morvalquist</span>
      <div class="social-icons">
        <span></span><span></span><span></span><span></span>
      </div>
    </div>
  </section>
</main>
</body>
</html>
```